Residential Remodeling Contractor needs updated business card

I need a new design for my business card.
Name of the company is Ridgefell Construction. I need a card that commands presence, strength, integrity. I have been in business for 28 years. I am a Residential Remodeling Contractor that covers all aspects of a residential remodel and build.

```html
<!DOCTYPE html>
<html lang="en">
<head>
<meta charset="utf-8">
<title>Ridgefell Construction – Business Card</title>
<link rel="stylesheet" href="https://fonts.googleapis.com/css2?family=Montserrat:wght@400;500;600&family=Oswald:wght@600&display=swap">
<style>
  :root {
    --backdrop: #d9d9d7;
    --card-blue: #203d7c;
    --mark-blue: #3f6fd8;
    --ink-white: #ffffff;
    --card-shadow: rgba(0, 0, 0, 0.28);
  }
  * { box-sizing: border-box; margin: 0; padding: 0; }
  html, body {
    width: 1200px;
    height: 801px;
    overflow: hidden;
    background: var(--backdrop);
  }
  .canvas {
    position: relative;
    width: 1200px;
    height: 801px;
    display: flex;
    align-items: center;
    justify-content: center;
    gap: 50px;
  }
  .card {
    position: relative;
    width: 530px;
    height: 303px;
    background: var(--card-blue);
    color: var(--ink-white);
    box-shadow: 0 14px 30px var(--card-shadow);
    font-family: "Montserrat", sans-serif;
  }

  /* Front side */
  .brand {
    position: absolute;
    left: 120px;
    top: 52px;
    display: flex;
    align-items: center;
    gap: 12px;
  }
  .brand-square {
    width: 14px;
    height: 14px;
    background: var(--ink-white);
  }
  .brand-name {
    font-family: "Montserrat", sans-serif;
    font-weight: 600;
    font-size: 22px;
    line-height: 1.1;
    letter-spacing: 0.08em;
    text-transform: uppercase;
    color: var(--ink-white);
  }
  .details {
    position: absolute;
    left: 48px;
    top: 142px;
    display: flex;
    align-items: center;
  }
  .person { text-align: right; padding-right: 20px; }
  .person-name {
    font-family: "Oswald", sans-serif;
    font-weight: 600;
    font-size: 34px;
    line-height: 1;
    letter-spacing: 0.01em;
    text-transform: uppercase;
  }
  .person-role {
    font-size: 12px;
    font-weight: 500;
    margin-top: 3px;
  }
  .divider {
    width: 1px;
    height: 62px;
    background: var(--ink-white);
  }
  .contact-list {
    list-style: none;
    padding-left: 20px;
    font-size: 11.5px;
    line-height: 1.55;
  }
  .contact-list li { display: flex; align-items: center; gap: 6px; }
  .contact-list svg { width: 10px; height: 10px; flex: none; }
  .address {
    position: absolute;
    left: 0;
    right: 0;
    bottom: 48px;
    text-align: center;
    font-size: 12.5px;
    font-weight: 500;
    letter-spacing: 0.02em;
  }

  /* Back side */
  .back-brand {
    position: absolute;
    left: 110px;
    top: 92px;
    display: flex;
    align-items: center;
    gap: 16px;
  }
  .back-brand-square {
    width: 22px;
    height: 22px;
    background: var(--mark-blue);
  }
  .back-brand-name {
    font-family: "Montserrat", sans-serif;
    font-weight: 600;
    font-size: 30px;
    line-height: 1.1;
    letter-spacing: 0.08em;
    text-transform: uppercase;
    color: var(--mark-blue);
  }
  .tagline {
    position: absolute;
    right: 40px;
    bottom: 72px;
    font-size: 11px;
    font-weight: 600;
    letter-spacing: 0.06em;
    text-transform: uppercase;
  }
</style>
</head>
<body>
<main class="canvas">
  <section class="card card-front" aria-label="Card front">
    <div class="brand">
      <span class="brand-square"></span>
      <span class="brand-name">Ridgefell<br>Construction</span>
    </div>
    <div class="details">
      <div class="person">
        <p class="person-name">Marcus Delane</p>
        <p class="person-role">Director</p>
      </div>
      <span class="divider"></span>
      <ul class="contact-list">
        <li>
          <svg viewBox="0 0 10 10" aria-hidden="true"><path d="M2 1 L3.6 1 L4.2 3 L3.2 3.8 Q4 5.8 6.2 6.8 L7 5.8 L9 6.4 L9 8 Q8.5 9 7.5 9 Q1 8 1 2.5 Q1 1 2 1 Z" fill="#fff"/></svg>
          (555) 014-2276
        </li>
        <li>
          <svg viewBox="0 0 10 10" aria-hidden="true"><rect x="0.7" y="2" width="8.6" height="6" fill="none" stroke="#fff" stroke-width="1"/><path d="M0.7 2 L5 5.4 L9.3 2" fill="none" stroke="#fff" stroke-width="1"/></svg>
          info@ridgefellbuild.com
        </li>
        <li>
          <svg viewBox="0 0 10 10" aria-hidden="true"><circle cx="5" cy="5" r="4.3" fill="none" stroke="#fff" stroke-width="0.9"/><ellipse cx="5" cy="5" rx="1.8" ry="4.3" fill="none" stroke="#fff" stroke-width="0.8"/><path d="M0.7 5 H9.3 M1.5 2.8 H8.5 M1.5 7.2 H8.5" stroke="#fff" stroke-width="0.7"/></svg>
          www.ridgefellbuild.com
        </li>
      </ul>
    </div>
    <p class="address">48 Harlow Lane Brookfield, GA 30000</p>
  </section>

  <section class="card card-back" aria-label="Card back">
    <div class="back-brand">
      <span class="back-brand-square"></span>
      <span class="back-brand-name">Ridgefell<br>Construction</span>
    </div>
    <p class="tagline">I have been in business for 28 years</p>
  </section>
</main>
</body>
</html>
```